Website Redesign - We Need Your Magic!

Hello we are looking for you to help us re-design a high end and professional website for a high-end private school.

Here is the current site: http://www.ferndalecrest.com/

NOTE THIS IS DESIGN ONLY, NO CODING :)

The image they want to portray is that of high quality sports and education, in a creative "un-stiff" way.

Menu Bar: Horizontal

Look and Feel:

Site Colors: Dark green and a Gold yellow (logos are attached)

This site will represent a school so the look must be clean, bold, and classy. The site must have a very clean user interface, with things easily recognizable. Think simple.

The site should be visually appealing! If you come to me with templates, or a ton of text you will be out.

This site should be outside the box, we do not want boring, we do not want status quo. This site should instill excitement, innovation, and athletics.

So the main points again are:

1. High-end and classy look, with creative feel
2. Simple and clear navigation style
3. To cover the Junior and High School - Ferndale Crest College Schools

Think outside the box. We look forward to seeing what you come up with!!

Thank you for helping us create an amazing site for the school!

Industry/Entity Type

School

```html
<!DOCTYPE html>
<html lang="en">
<head>
<meta charset="utf-8">
<title>Ferndale Crest College</title>
<link href="https://fonts.googleapis.com/css2?family=Arimo:ital,wght@0,400;0,700;1,400;1,700&family=Montserrat:wght@600&display=swap" rel="stylesheet">
<style>
:root{
  --green:#145a20;
  --green-dark:#0d3d14;
  --green-head:#1d5a26;
  --gold:#c1a913;
  --gold-bright:#e2cd1c;
  --gold-text:#b08a14;
  --ink:#222;
  --muted:#555;
  --rule:#d6d6d6;
  --footer:#2b2b2b;
  --footer-base:#1d1d1d;
}
*{margin:0;padding:0;box-sizing:border-box}
html,body{width:875px;height:1200px;overflow:hidden;background:#fff}
body{font-family:"Arimo",Arial,sans-serif;color:var(--ink);position:relative;font-size:10.4px}
.abs{position:absolute}

/* header */
.site-header{position:absolute;left:0;top:0;width:875px;height:111px;background:linear-gradient(#f7f7f7,#fff)}
.crest-mark{left:76px;top:18px;width:64px;height:64px;border-radius:50%;background:var(--green);border:4px solid var(--gold-bright)}
.site-name{left:165px;top:35px;font-family:"Montserrat",sans-serif;font-weight:600;font-size:23px;color:var(--green)}
.tagline{left:165px;top:72px;font-size:11px;color:#333}
.contact{left:510px;top:32px;font-size:10.5px;color:#333;display:flex;gap:14px;align-items:center;white-space:nowrap}
.contact span{display:flex;align-items:center;gap:6px}
.search{left:507px;top:63px;width:295px;height:27px;display:flex}
.search .field{flex:1;border:1px solid #ccc;background:#fff;font-size:10px;color:#777;padding:7px 8px}
.search .btn{width:60px;background:var(--green-dark);color:#fff;font-weight:700;font-size:9.5px;display:flex;align-items:center;justify-content:center;gap:4px}

/* nav */
.main-nav{position:absolute;left:0;top:111px;width:875px;height:34px;background:linear-gradient(#1f7a2c,#0f3f15)}
.main-nav ul{list-style:none;display:flex;justify-content:space-between;position:absolute;left:73px;width:729px;height:34px}
.main-nav li{color:#fff;font-weight:700;font-size:9.8px;line-height:34px;white-space:nowrap}
.main-nav li.active{background:var(--gold-bright);color:#111;padding:0 15px}

/* hero */
.hero{left:73px;top:158px;width:497px;height:256px;background:linear-gradient(160deg,#b8c6cc 0%,#8a9a78 45%,#5d6e3d 100%)}
.hero-arrow{position:absolute;top:106px;width:26px;height:26px;border-radius:50%;background:#111}
.hero-dots{position:absolute;left:0;bottom:0;width:100%;height:33px;background:rgba(0,0,0,.45)}
.dot{position:absolute;top:7px;width:19px;height:19px;border:1.5px solid #fff;color:#fff;font-weight:700;font-size:12px;text-align:center;line-height:16px;background:var(--green-dark)}
.dot.on{background:var(--gold)}
.newsletter{left:570px;top:158px;width:232px;height:256px;background:var(--gold);padding:28px 20px 0 21px;color:#fff}
.newsletter h2{font-size:17.5px;color:#111;font-weight:700;margin-bottom:11px}
.newsletter p{font-size:9.3px;line-height:13px;margin-bottom:13px}
.newsletter .input{background:#fff;color:#333;font-size:10px;height:23px;padding:6px 8px;margin-bottom:19px;width:190px}
.newsletter .sub{position:absolute;right:19px;top:195px;background:var(--green-dark);color:#fff;font-weight:700;font-size:11.5px;padding:5px 8px;border-radius:3px}

/* main column */
.main{left:74px;top:433px;width:458px}
.main h1,.head-title{font-weight:400;font-size:19.5px;color:var(--gold-text);margin-bottom:10px}
.head-title{left:73px;top:673px}
.main p,.head-text p,.closing p{font-size:10.4px;line-height:16px;color:#222;margin-bottom:16px;letter-spacing:.3px}
.head-note{left:73px;top:709px;width:136px;height:170px;background:linear-gradient(90deg,#2d6a3a,#9b8c70 50%,#2d6a3a)}
.head-text{left:218px;top:706px;width:318px}
.closing{left:74px;top:902px;width:464px}

/* sidebar */
.side{left:578px;top:433px;width:226px}
.side-block{border-bottom:1px solid var(--rule);padding:0 6px 10px 6px;position:relative}
.side-block h3{font-weight:400;font-size:18px;color:var(--green-head);margin-bottom:8px}
.pager{position:absolute;right:6px;top:5px;display:flex;gap:3px}
.pager i{width:12px;height:12px;background:#e4e4e4;border:1px solid #ccc;border-radius:2px}
.cal li{list-style:none;font-size:9.6px;line-height:17.5px;color:#333}
.event{padding:6px 0 6px;border-bottom:1px solid var(--rule);font-size:9.4px}
.event:last-child{border:0}
.event b{color:var(--green-dark);display:block}
.event em{color:var(--gold-text);display:block;margin:2px 0}
.upcoming .item{font-size:9.4px;line-height:13px;padding:5px 0;border-bottom:1px solid var(--rule)}
.upcoming .item:last-child{border:0}
.upcoming em{display:block;text-align:right;color:var(--gold-text);font-weight:700;font-size:8.5px}

.social{left:589px;top:848px;width:213px;height:198px;border:1px solid #aab;font-size:8px;color:#333;background:#fff}
.social-top{height:23px;background:#3b5797;color:#fff;display:flex;justify-content:space-between;align-items:center;padding:0 7px;font-size:8.5px}
.social-top b{font-size:10px}
.page{display:flex;gap:8px;padding:6px;border-bottom:1px solid #ddd}
.sq{width:34px;height:34px;background:var(--green);flex:none}
.page-name{color:#3b5797;font-size:9.5px;font-weight:700}
.feed{display:flex;gap:8px;padding:7px 6px;height:56px;border-bottom:1px solid #ddd;font-size:8.5px}
.feed .sq{background:#bbb}
.fans{padding:5px 6px;font-size:8px}
.faces{display:flex;gap:4px;margin-top:4px}
.faces i{width:35px;height:35px;background:linear-gradient(#c9a58c,#6d5646)}
.plugin{padding:3px 6px;font-size:7px;color:#555}

/* footer */
.site-footer{left:0;top:1063px;width:875px;height:112px;background:var(--footer);color:#fff}
.foot-name{left:153px;top:22px;font-weight:700;font-size:13px;white-space:nowrap}
.foot-addr{left:153px;top:40px;width:124px;text-align:right;font-size:9px;line-height:13px}
.foot-link{left:147px;top:70px;font-size:8.5px;text-decoration:underline}
.foot-dl{left:413px;top:25px}
.foot-dl h4{font-size:12px;margin-bottom:9px}
.foot-dl p{font-size:9.5px;line-height:16px}
.foot-crest{left:666px;top:25px;display:flex;align-items:center;gap:6px;color:#5a5a5a;font-size:11px;font-weight:700}
.foot-crest i{width:34px;height:34px;border:2px solid #5a5a5a;border-radius:50%}
.copyright{left:0;top:1175px;width:875px;height:25px;background:var(--footer-base);color:#bbb;font-size:9.5px;text-align:center;line-height:25px}
</style>
</head>
<body>

<header class="site-header">
  <div class="abs crest-mark"></div>
  <div class="abs site-name">Ferndale Crest College</div>
  <div class="abs tagline">Stepping Ahead in . Eduction . Culture &nbsp;. &nbsp;Sport . &nbsp;Life</div>
  <div class="abs contact">
    <span><svg width="11" height="11" viewBox="0 0 24 24"><path fill="#0d3d14" d="M6.6 10.8a15 15 0 0 0 6.6 6.6l2.2-2.2c.3-.3.7-.4 1-.2 1.1.4 2.3.6 3.6.6.6 0 1 .4 1 1V20c0 .6-.4 1-1 1A17 17 0 0 1 3 4c0-.6.4-1 1-1h3.5c.6 0 1 .4 1 1 0 1.3.2 2.5.6 3.6.1.3 0 .7-.2 1z"/></svg>0700 481 226 / 0700 481 337</span>
    <span><svg width="13" height="9" viewBox="0 0 13 9"><rect width="13" height="9" fill="#e2b43a"/><path d="M0 0l6.5 5L13 0" stroke="#fff" fill="none"/></svg>office@ferndalecrest.com</span>
  </div>
  <div class="abs search">
    <div class="field">Search you any keyword</div>
    <div class="btn"><svg width="9" height="9" viewBox="0 0 10 10"><circle cx="4" cy="4" r="3" stroke="#fff" fill="none" stroke-width="1.4"/><path d="M6.3 6.3L9 9" stroke="#fff" stroke-width="1.4"/></svg>Search</div>
  </div>
</header>

<nav class="main-nav">
  <ul>
    <li class="active">HOME</li><li>ABOUT US</li><li>ACADEMICS</li><li>SPORTS</li><li>JOINING FERNDALE CREST</li><li>WORKING AT THE COLLEGE</li><li>CONTACT US</li>
  </ul>
</nav>

<section class="abs hero" role="img" aria-label="Photo of the school cricket team in whites posing with their coach on the field">
  <div class="hero-arrow" style="left:12px"><svg width="26" height="26"><path d="M15 8l-5 5 5 5" stroke="#e2cd1c" stroke-width="2.5" fill="none"/></svg></div>
  <div class="hero-arrow" style="right:6px"><svg width="26" height="26"><path d="M11 8l5 5-5 5" stroke="#e2cd1c" stroke-width="2.5" fill="none"/></svg></div>
  <div class="hero-dots">
    <div class="dot" style="left:410px">1</div>
    <div class="dot on" style="left:439px">2</div>
    <div class="dot" style="left:467px">3</div>
  </div>
</section>

<aside class="abs newsletter">
  <h2>Subscribe Newsletter</h2>
  <p>If you would like to be added to the list of parents that receive the School Newsletter, please enter your details below.</p>
  <div class="input">Your Name</div>
  <div class="input">Email Address</div>
  <div class="sub">SUBSCRIBE</div>
</aside>

<main class="abs main">
  <h1>Welcome to Ferndale Crest College</h1>
  <p>Welcome to Ferndale Crest Group of Schools where our School Motto is ‘Sekuru’ meaning Togetherness. We aim to work together in every aspect of School life, from academics to sport.</p>
  <p>Ferndale Crest College opened on 14th February 1983 and occupies 120 ha of land amidst the low hills of the Marula Range, 8km west of Kestrel Falls. This location encourages focus on School life away from the distractions and hustle and bustle of the larger towns.</p>
  <p>The day scholars have the option of selected bus drop off points for parents to collect day scholars closer to home. Ferndale Crest College offers a wide range of academic subjects alongside a varied sport and extra-curricular program.</p>
</main>

<h2 class="abs head-title">Headmaster's Welcome Note</h2>
<div class="abs head-note" role="img" aria-label="Portrait photo of the headmaster"></div>
<div class="abs head-text">
  <p>Welcome to Ferndale Crest College. &nbsp;Here at the College we aim to encourage each pupil to be a self-confident, well-rounded individual. &nbsp;We aim to propel them to the highest level of achievement in both academics and extra-curricular activities to provide them with the life skills they will need when they leave the College and to prepare them to be of value to society.</p>
  <p>The College is a warm community which lives out high standards and is rightly proud of its achievements. &nbsp;We are a small enough School for each pupil to be known well, but large enough to offer a wide range of subjects and experience.</p>
</div>
<div class="abs closing">
  <p>Our Website covers many aspects of the College from how to apply for a place, to the curriculum and to much more. &nbsp;I hope you find it helpful and interesting. &nbsp;Please visit and meet the pupils, the staff and see for yourself what Ferndale Crest College can offer your son or daughter. &nbsp;I look forward to welcoming you and your family to Ferndale Crest College.</p>
</div>

<aside class="abs side">
  <div class="side-block">
    <h3>School Calender</h3><div class="pager"><i></i><i></i></div>
    <ul class="cal">
      <li>Begins: Tuesday 14th January</li>
      <li>1st Fixture Free: Friday 31st January</li>
      <li>Half-Term: Thursday 20th February</li>
      <li>Term Ends: Thursday &nbsp;10th April</li>
    </ul>
  </div>
  <div class="side-block" style="padding-top:10px">
    <h3>School Events</h3><div class="pager" style="top:15px"><i></i><i></i></div>
    <div class="event"><b>Ferndale Crest Group of Schools Motto</b><em>January 21, 2014</em>Lorem Ipsum is simply dummy text the printing .</div>
    <div class="event"><b>Ferndale Crest Group of Schools Motto</b><em>January 21, 2014</em>Lorem Ipsum is simply dummy text the printing .</div>
  </div>
  <div class="side-block upcoming" style="padding-top:10px;border:0">
    <h3>Upcoming Events</h3><div class="pager" style="top:15px"><i></i><i></i></div>
    <div class="item"><em>Mon 04 Aug</em>When an unknown printer took a galley of type and scra mbled it specimen book.</div>
    <div class="item"><em>Mon 04 Aug</em>When an unknown printer took a galley of type and scra mbled it specimen book.</div>
  </div>
</aside>

<div class="abs social">
  <div class="social-top"><span>Find us on Friendsfeed</span><b>Friendsfeed</b></div>
  <div class="page"><div class="sq"></div><div><div class="page-name">Campus Corner</div><div style="margin-top:5px">✓ Like &nbsp;You like this.</div></div></div>
  <div class="feed"><div class="sq"></div><div><div class="page-name">Campus Corner</div>"The idea of a culinary contest one either."</div></div>
  <div class="fans">30,821 people like <b>Campus Corner</b>.
    <div class="faces" role="img" aria-label="Row of follower profile photos"><i></i><i></i><i></i><i></i><i></i></div>
  </div>
  <div class="plugin">Friendsfeed social plugin</div>
</div>

<footer class="abs site-footer">
  <svg class="abs" style="left:102px;top:20px" width="32" height="45" viewBox="0 0 32 45"><path d="M16 0C7 0 0 7 0 16c0 12 16 29 16 29s16-17 16-29C32 7 25 0 16 0z" fill="#f2a531"/><circle cx="16" cy="16" r="6" fill="#2b2b2b"/></svg>
  <div class="abs foot-name">Ferndale Crest College</div>
  <div class="abs foot-addr">12 Oakmere Road,<br>Brackenhill 4021</div>
  <div class="abs foot-link">Click here to see the directions &gt;&gt;</div>
  <div class="abs foot-dl"><h4>Download</h4><p>Registration Form<br>2nd Term 2014 Termly Calendar</p></div>
  <div class="abs foot-crest"><i></i>Ferndale Crest</div>
</footer>
<div class="abs copyright">Copyright © 2014 Ferndale Crest. All Rights Reserved.</div>

</body>
</html>
```